Business Card for a mobile physiotherapy company

I need a layout for a business card for a mobile physiotherapy company.
Slogan is "Mobile Physiotherapy - Your Road To Recovery"
Phone number is 867-555-0142
Email VardenTherapy@postnest.ca (subject to change with website)
Website www.VardenTherapy.ca
My name and credentials: Luke Varden Luke Varden, BSc(kin), MPT, CAFCI, IMS
Information maybe included: Direct Billing, Services including Physiotherapy, IMS, acupuncture
Maybe include facebook and instagram logos
One side with the logo clean and sharp
Other side with details, try not to look too busy, keep everything concise

```html
<!DOCTYPE html>
<html lang="en">
<head>
<meta charset="utf-8">
<title>Varden Therapy Business Card</title>
<link rel="stylesheet" href="https://fonts.googleapis.com/css2?family=Lato:wght@400;700&family=Roboto:wght@400&display=swap">
<style>
  :root {
    --navy: #2b4a78;
    --navy-deep: #233f69;
    --green: #1d5e4a;
    --white: #ffffff;
    --stage: #b9b9b9;
  }
  * { box-sizing: border-box; margin: 0; padding: 0; }
  html, body { width: 1200px; height: 930px; overflow: hidden; }
  body {
    background: var(--stage);
    position: relative;
    font-family: "Lato", sans-serif;
  }
  .card {
    position: absolute;
    width: 640px;
    height: 366px;
    border-radius: 26px;
    overflow: hidden;
    box-shadow: 0 6px 18px rgba(0,0,0,0.25);
  }
  .card-front {
    left: 60px; top: 50px;
    background: var(--navy);
    color: var(--white);
  }
  .card-back {
    left: 500px; top: 510px;
    background: var(--white);
  }
  .front-brand {
    position: absolute;
    left: 0; right: 0; top: 120px;
    display: flex; align-items: center; justify-content: center; gap: 14px;
    font-size: 42px; font-weight: 700; letter-spacing: 3px;
    color: var(--white);
  }
  .brand-mark {
    width: 26px; height: 26px;
    background: currentColor;
  }
  .front-slogan {
    position: absolute;
    left: 0; right: 0; bottom: 48px;
    text-align: center;
    font-size: 19px;
    color: var(--white);
  }
  .back-brand {
    position: absolute;
    left: 36px; top: 120px;
    display: flex; align-items: center; gap: 10px;
    font-size: 30px; font-weight: 700; letter-spacing: 2px;
    color: var(--navy);
  }
  .back-brand .brand-mark { width: 20px; height: 20px; }
  .identity {
    position: absolute;
    right: 40px; top: 36px;
    text-align: right;
  }
  .identity-name {
    font-family: "Roboto", sans-serif;
    font-size: 27px;
    line-height: 1.2;
    color: var(--navy);
  }
  .identity-services {
    margin-top: 8px;
    font-size: 16px;
    line-height: 1.35;
    color: var(--green);
  }
  .identity-rule {
    position: absolute;
    right: 40px; top: 174px;
    width: 330px; height: 2px;
    background: var(--navy);
  }
  .contact-rule {
    position: absolute;
    left: 36px; top: 222px;
    width: 300px; height: 2px;
    background: var(--navy);
  }
  .contact-list {
    position: absolute;
    left: 36px; top: 236px;
    list-style: none;
  }
  .contact-list li {
    display: flex; align-items: center; gap: 12px;
    font-size: 18px; line-height: 27px;
    color: var(--navy);
  }
  .contact-list svg { width: 13px; height: 13px; fill: var(--navy); }
  .band {
    position: absolute;
    left: 0; bottom: 0;
    width: 640px; height: 130px;
  }
</style>
</head>
<body>
  <section class="card card-front">
    <div class="front-brand"><span class="brand-mark"></span>VARDEN THERAPY</div>
    <p class="front-slogan">Mobile Physiotherapy - Your Road To Recovery</p>
  </section>

  <section class="card card-back">
    <svg class="band" viewBox="0 0 640 130" preserveAspectRatio="none" aria-hidden="true">
      <path d="M330 130 L470 40 Q500 20 540 20 L640 20 L640 130 Z" fill="var(--navy)"/>
      <path d="M330 130 L462 50 L470 46 L346 130 Z" fill="var(--white)"/>
      <path d="M320 130 L455 50 L462 50 L332 130 Z" fill="var(--green)"/>
    </svg>

    <div class="back-brand"><span class="brand-mark"></span>VARDEN THERAPY</div>

    <div class="identity">
      <h1 class="identity-name">Luke Varden, BSc(kin),<br>MPT, CAFCI, IMS</h1>
      <p class="identity-services">Direct Billing, Services including<br>Physiotherapy, IMS, acupuncture</p>
    </div>
    <div class="identity-rule"></div>

    <div class="contact-rule"></div>
    <ul class="contact-list">
      <li><svg viewBox="0 0 24 24" aria-hidden="true"><path d="M6.6 10.8a15 15 0 0 0 6.6 6.6l2.2-2.2c.3-.3.7-.4 1-.2 1.1.4 2.3.6 3.6.6.6 0 1 .4 1 1V20c0 .6-.4 1-1 1A17 17 0 0 1 3 4c0-.6.4-1 1-1h3.5c.6 0 1 .4 1 1 0 1.3.2 2.5.6 3.6.1.3 0 .7-.2 1z"/></svg>867-555-0142</li>
      <li><svg viewBox="0 0 24 24" aria-hidden="true"><path d="M2 5h20v14H2z M4 7v1l8 5 8-5V7l-8 5z" fill-rule="evenodd"/></svg>VardenTherapy@postnest.ca</li>
      <li><svg viewBox="0 0 24 24" aria-hidden="true"><circle cx="12" cy="12" r="10"/></svg>www.VardenTherapy.ca</li>
    </ul>
  </section>
</body>
</html>
```